Design and Renovation Company Luxury Business Card

I want to create a luxury business card for a Design and Renovation Firm . We will use our current logo. The company name is 528BUILDA. We do not want anything standard. We need a very unique concept.
Please see uploaded inspiration. I really like the textured paper option. I would like the card to be thick with debossing, and/or embossing options. The logo has orange in it but I would like to see the card with and without the orange. I think the orange may make the company feel less high-end. The goal is to elevate the logo not match its vibe per se of the logo. We want something very unique, not standard at all!
I would like a space for :
Logo,
Name,
Position,
Email,
Office number,
Website Address,
Business Address,
Thank you!
Have fun!
Target Market(s)
Home owners Age 35 +
Industry/Entity Type
Design and Renovation
Contact Information for Business Card
Logo, Name, Position, Email, Office number, Website Address, Business Address,.
Colors
Designer to choose colors to be used in the design.
Requirements
Must have
- A luxury designer feel. Must be black or dark grey but open to other luxury ideas.
Nice to have
- Gold, silver, black embossing or debossing. Textured paper design.
Should not have
- A cheap look and feel.

```html
<!DOCTYPE html>
<html lang="en">
<head>
<meta charset="UTF-8">
<title>528BUILDA Business Card</title>
<link href="https://fonts.googleapis.com/css2?family=Roboto:wght@300;400;500&display=swap" rel="stylesheet">
<style>
  :root {
    --page: #8a8a8a;
    --card: #0b0b0b;
    --card-edge: #1a1a1a;
    --orange: #f7941d;
    --white: #ffffff;
    --grey-text: #c9c9c9;
    --muted: #a9a9a9;
    --silver: #d4d4d4;
    --deboss: rgba(255,255,255,0.07);
  }
  * { margin: 0; padding: 0; box-sizing: border-box; }
  html, body { width: 1093px; height: 1200px; overflow: hidden; }
  body {
    background: var(--page);
    font-family: "Roboto", Arial, sans-serif;
    position: relative;
  }
  .card {
    position: absolute;
    left: 265px;
    width: 580px;
    height: 358px;
    border-radius: 24px;
    background: radial-gradient(ellipse at 20% 20%, #1b1b1b 0%, var(--card) 60%, #050505 100%);
    box-shadow: 0 3px 0 var(--card-edge);
    overflow: hidden;
  }
  .card--front { top: 226px; }
  .card--back { top: 620px; }

  .grid-line { position: absolute; background: var(--deboss); }
  .grid-line--vertical { left: 192px; top: 0; width: 2px; height: 100%; }
  .grid-line--horizontal { left: 0; top: 192px; width: 354px; height: 2px; }
  .grid-band { position: absolute; left: 162px; top: 0; width: 30px; height: 100%; background: rgba(255,255,255,0.025); }

  .person { position: absolute; left: 25px; top: 46px; }
  .person__name { color: var(--orange); font-weight: 500; font-size: 24px; line-height: 1; }
  .person__role { color: var(--muted); font-size: 17px; font-weight: 400; margin-top: 2px; }

  .brand { position: absolute; display: flex; flex-direction: column; }
  .brand__name { font-weight: 300; line-height: 1; }
  .brand__line { font-weight: 400; text-transform: uppercase; }

  .card--front .brand { right: 40px; top: 50px; align-items: flex-end; }
  .card--front .brand__name { font-size: 34px; letter-spacing: 0.08em; color: var(--white); }
  .card--front .brand__line { font-size: 9px; letter-spacing: 0.3em; color: var(--muted); margin-top: 6px; }

  .contacts { position: absolute; left: 25px; top: 261px; list-style: none; }
  .contacts li { display: flex; align-items: center; gap: 6px; color: var(--grey-text); font-size: 17px; height: 21px; }
  .contacts svg { width: 15px; height: 15px; flex: none; }
  .accent { color: var(--orange); }

  .address { position: absolute; right: 28px; top: 280px; text-align: right; color: var(--grey-text); font-size: 17px; line-height: 21px; font-style: normal; }

  .card--back .brand { left: 0; right: 0; top: 152px; align-items: center; }
  .card--back .brand__name { font-size: 50px; letter-spacing: 0.1em; color: var(--silver); }
  .card--back .brand__line { font-size: 12px; letter-spacing: 0.4em; color: var(--muted); margin-top: 10px; }
</style>
</head>
<body>
  <section class="card card--front">
    <div class="grid-band"></div>
    <div class="grid-line grid-line--vertical"></div>
    <div class="grid-line grid-line--horizontal"></div>

    <div class="person">
      <h1 class="person__name">DANIEL MARSH</h1>
      <p class="person__role">Managing Director</p>
    </div>

    <div class="brand">
      <span class="brand__name">528BUILDA</span>
      <span class="brand__line">Interiors &amp; Renovation</span>
    </div>

    <ul class="contacts">
      <li>
        <svg viewBox="0 0 16 16" aria-hidden="true"><path fill="#f7941d" d="M3.5 1.5l2.5 3-1.5 1.5c.8 1.9 2.3 3.4 4.2 4.2L10.2 8.7l3 2.5-1.5 2.8C6.8 13.8 2.2 9.2 2 4.3z"/></svg>
        044-987 654 321
      </li>
      <li>
        <svg viewBox="0 0 16 16" aria-hidden="true"><rect x="1" y="3" width="14" height="10" fill="#f7941d"/><path d="M1 3l7 6 7-6" fill="none" stroke="#0b0b0b" stroke-width="1.3"/></svg>
        info@webname.com
      </li>
      <li>
        <svg viewBox="0 0 16 16" aria-hidden="true"><g fill="none" stroke="#f7941d" stroke-width="1.4"><circle cx="8" cy="8" r="6.5"/><ellipse cx="8" cy="8" rx="3" ry="6.5"/><path d="M1.5 8h13M2.5 5h11M2.5 11h11"/></g></svg>
        <span>www.<span class="accent">websitename</span>.com</span>
      </li>
    </ul>

    <address class="address">421, Address line goes here<br>45452,Country Name</address>
  </section>

  <section class="card card--back">
    <div class="brand">
      <span class="brand__name">528BUILDA</span>
      <span class="brand__line">Interiors &amp; Renovation</span>
    </div>
  </section>
</body>
</html>
```